Veranix - Solution provider in business consulting

Veranix is a swiss based company providing solutions for developing markets. The business covers various fields of business consulting, such as supply chain, product costs, quality management and manufacturing management. The Business operates in a efficient, straight and solution oriented manner.
The final design should communicate these characteristics. Asian people as well as as western people shall identify the qualities of the company at first sight.
The customer needs business cards with a simple view but an recognizable design, printed in high quality. Engraved elements such as the globe or simple words are possible.
Available colors are: (RAL)
102/102/102
51/102/102
153/204/153
255/102/51
Font: Calibri

```html
<!DOCTYPE html>
<html lang="en">
<head>
<meta charset="utf-8">
<title>Veranix – Business Cards</title>
<link rel="stylesheet" href="https://fonts.googleapis.com/css2?family=Carlito:wght@400;700&display=swap">
<style>
  :root {
    --brand-grey: #666666;
    --paper: #ffffff;
    --backdrop: #e9e9e7;
    --ink: #1f1f1f;
  }
  html, body {
    margin: 0;
    padding: 0;
    width: 1200px;
    height: 900px;
    overflow: hidden;
    background: var(--backdrop);
    font-family: "Carlito", "Calibri", sans-serif;
  }
  .stage {
    position: relative;
    width: 1200px;
    height: 900px;
  }
  .card {
    position: absolute;
    border-radius: 16px;
    overflow: hidden;
    box-shadow: 0 6px 18px rgba(0,0,0,0.12);
  }
  /* Front */
  .card-front {
    left: 77px; top: 35px;
    width: 588px; height: 363px;
    background: var(--paper);
  }
  .card-front .band {
    position: absolute;
    left: 0; top: 28px;
    width: 100%; height: 99px;
    background: var(--brand-grey);
  }
  .emblem {
    position: absolute;
    border-radius: 50%;
    background: var(--brand-grey);
    box-sizing: border-box;
  }
  .card-front .emblem {
    left: 217px; top: -18px;
    width: 164px; height: 164px;
    border: 7px solid var(--paper);
  }
  .wordmark {
    position: absolute;
    left: 0; width: 100%;
    text-align: center;
    font-weight: 400;
    letter-spacing: 1px;
    line-height: 1;
  }
  .card-front .wordmark {
    top: 142px;
    font-size: 74px;
    color: var(--brand-grey);
  }
  .person {
    position: absolute;
    left: 46px; top: 232px;
    color: var(--ink);
  }
  .person-name {
    font-size: 22px;
    font-weight: 700;
    color: var(--brand-grey);
    margin: 0;
  }
  .person-role {
    font-size: 16px;
    margin: 2px 0 0;
  }
  .address {
    font-size: 16px;
    line-height: 22px;
    margin: 20px 0 0;
  }
  .contacts {
    position: absolute;
    right: 36px; top: 240px;
    margin: 0; padding: 0;
    list-style: none;
    font-size: 16px;
    color: var(--ink);
  }
  .contacts li {
    display: flex;
    justify-content: flex-end;
    align-items: center;
    height: 24.5px;
  }
  .contacts svg {
    width: 12px; height: 12px;
    margin-left: 8px;
    fill: var(--brand-grey);
  }
  /* Back */
  .card-back {
    left: 390px; top: 505px;
    width: 565px; height: 350px;
    background: var(--brand-grey);
  }
  .card-back .band {
    position: absolute;
    left: 0; top: 80px;
    width: 100%; height: 100px;
    background: var(--paper);
  }
  .card-back .emblem {
    left: 210px; top: 66px;
    width: 120px; height: 120px;
  }
  .card-back .wordmark {
    top: 198px;
    font-size: 74px;
    color: var(--paper);
  }
  .card-back .web {
    position: absolute;
    left: 0; width: 100%;
    top: 295px;
    text-align: center;
    font-size: 17px;
    font-weight: 700;
    color: var(--paper);
  }
</style>
</head>
<body>
<main class="stage">
  <section class="card card-front" aria-label="Business card front">
    <div class="band"></div>
    <div class="emblem"></div>
    <div class="wordmark">veranix</div>
    <div class="person">
      <p class="person-name">Marten Holzer</p>
      <p class="person-role">CEO</p>
      <p class="address">Veranix GmbH Lindenweg 14<br>9230 Flawil Switzerland</p>
    </div>
    <ul class="contacts">
      <li>+41 79 382 5716
        <svg viewBox="0 0 12 12" aria-hidden="true"><path d="M3 0h6a1 1 0 0 1 1 1v10a1 1 0 0 1-1 1H3a1 1 0 0 1-1-1V1a1 1 0 0 1 1-1zm0 1.5v8h6v-8zm3 8.6a.7.7 0 1 0 0 1.4.7.7 0 0 0 0-1.4z"/></svg></li>
      <li>+41 71 648 2093
        <svg viewBox="0 0 12 12" aria-hidden="true"><path d="M2.4 0.6l1.8 2.2-1 1.3c.7 1.6 2 2.9 3.7 3.7l1.3-1 2.2 1.8-1 2.2C5 10.8 1.2 7 .8 1.6z"/></svg></li>
      <li>marten.holzer@veranix.ch
        <svg viewBox="0 0 12 12" aria-hidden="true"><path d="M0 2h12v8H0zm1 1v.4l5 3.2 5-3.2V3zm0 1.6V9h10V4.6L6 7.8z"/></svg></li>
      <li>www.veranix.ch
        <svg viewBox="0 0 12 12" aria-hidden="true"><circle cx="6" cy="6" r="6"/></svg></li>
    </ul>
  </section>

  <section class="card card-back" aria-label="Business card back">
    <div class="band"></div>
    <div class="emblem"></div>
    <div class="wordmark">veranix</div>
    <div class="web">www.veranix.ch</div>
  </section>
</main>
</body>
</html>
```